Website Design for a different kind of Business Consulting organisation needed!

We need a website design that reflects who we are, the simplicity of our consulting business and with a focus on our priority - to help our clients deliver, or execute - the "e" in Vantor-i.

Our key high level requirements are:
1) Simple and intuitive look and feel
2) Integration with all key social media platforms, twitter, facebook, linkedin, tumblr.

10 pages, tops.
- Main page - Welcome
- About Us/ Who are Vantor-i?
- 5 services pages - Project Management, Business Process Management, Change Management, Business Analysis and Finance Systems
- Contact Us

Something like:
http://www.lumvexhold.example/

Vantor-i is a registered trademark and all Logos and other branded material are attached for reference.

So, what’s our gig: A few snippets from previous work...

We are a different kind of business consulting group. We partner with our clients to help them deliver change. We don't just provide them with the theory. We also provide them with the leadership and capability to execute the change.

We aren’t a one stop shop, and we don’t offer cookie cutter solutions. We’re a boutique consulting firm covering Project Management, Business Process Management, Change Management and Business Analytics.

Vantor-i is a professional services organisation that partners with their clients to lead the execution of strategic process and system improvement initiatives. Vantor-i combines hands on delivery with coaching in best practice methodologies and approaches to build their clients capabilities to ensure their ongoing success in project implementations.

UPDATES:

Thanks to everyone who has submitted designs so far. The standard of designs coming through is quite high, with lots of professional designs that nail the design brief. Eliminating them is proving to be quite challenging.

A few updates to the job brief:
- Please make sure the design fits on one page. We would like all of our information to be on the first page that people see without them having to scroll down
- Please ensure you include the FIVE services we offer in the design
- Please use corporate images/istock photos in your designs which are relevant to our business
- Please add a section for a live twitter feed from our twitter account and a link to google+
- Please add a section for news/updates

Also, if you are able to build a site once a design is selected, please let us know.

Thanks,

Maribel.

Target Market(s)

Our target customers are large enterprises in Australia that are growing rapidly and have recently (last 24 months) undertaken or are currently undergoing software implementations and business process improvement programs. These businesses have a turnover of $100m or above and are working hard to differentiate themselves from their competitors but are not seeing the return on investment promised by software vendors and process improvement initiatives.

Industry/Entity Type

Leadership

Requirements
Must have
• Collaboration / Training / Workshop / Consulting images all of a professional nature.
Simple, non-cluttered look with plenty of white space.

```html
<!DOCTYPE html>
<html lang="en">
<head>
<meta charset="utf-8">
<title>Contact Us – Vantor-i</title>
<link rel="stylesheet" href="https://fonts.googleapis.com/css2?family=Lato:wght@700&family=Open+Sans:wght@400;600;700&display=swap">
<style>
:root{
  --brand:#0057a8;
  --ink:#444444;
  --muted:#9a9a9a;
  --icon-grey:#6e6e6e;
  --field:#f1f1f1;
  --field-line:#cfcfcf;
  --rule:#dddddd;
  --white:#ffffff;
}
*{box-sizing:border-box;margin:0;padding:0}
html,body{width:1200px;height:1046px;overflow:hidden;background:var(--white)}
body{font-family:"Open Sans",Arial,sans-serif;color:var(--ink)}
.page{position:relative;width:1200px;height:1046px;overflow:hidden}
.top-band{position:absolute;left:0;top:0;width:1200px;height:7px;background:var(--brand)}
.brand-name{position:absolute;left:120px;top:24px;font-size:50px;font-weight:600;color:var(--brand);letter-spacing:1px;line-height:1}
.social-top{position:absolute;top:17px;left:922px;display:flex;gap:9px}
.social-dot{width:32px;height:32px;border-radius:50%;background:var(--icon-grey)}
.social-dot.active{background:var(--brand)}
.main-nav{position:absolute;top:72px;left:560px;display:flex;font-family:"Lato",Arial,sans-serif;font-weight:700;font-size:15px}
.main-nav a{display:block;height:22px;line-height:22px;color:var(--muted);text-decoration:none;padding:0 16px;margin-right:10px}
.main-nav a.current{background:var(--brand);color:var(--white);padding:0 16px;margin-left:2px}
.header-rule{position:absolute;left:120px;top:116px;width:960px;height:1px;background:var(--rule)}
.page-title{position:absolute;left:120px;top:142px;font-size:26px;font-weight:700;color:var(--brand)}
.intro{position:absolute;left:120px;top:175px;width:960px;font-size:16px;line-height:25px}
.section-title{position:absolute;font-size:20px;font-weight:700;color:var(--ink)}
.contact-form{position:absolute;left:115px;top:288px;width:520px}
.contact-form .section-title{position:static;margin-bottom:8px}
.field-label{display:block;font-size:16px;margin-left:7px;line-height:22px}
.field{display:block;margin-left:6px;width:505px;height:33px;background:var(--field);border:1px solid var(--field-line);border-top-width:2px;border-left-width:2px;padding:0 13px;font-family:inherit;font-size:16px;color:#c4c4c4;line-height:31px;margin-top:4px}
.field + .field-label{margin-top:14px}
.field.message{height:139px;margin-top:3px;line-height:1;padding-top:7px}
.submit{position:absolute;left:391px;top:370px;width:119px;height:39px;background:var(--brand);color:var(--white);border:none;font-family:inherit;font-size:16px}
.details{position:absolute;left:767px;top:288px}
.details .section-title{position:static}
.address{margin-top:15px;font-size:16px;line-height:20px}
.detail-list{list-style:none;margin-top:13px}
.detail-list li{display:flex;align-items:center;height:30px;font-size:16px}
.detail-list svg{width:22px;height:22px;margin-right:9px}
.site-footer{position:absolute;left:0;top:928px;width:1200px;height:118px;background:var(--brand);color:var(--white);font-size:12.5px;line-height:19px}
.footer-col{position:absolute;top:19px}
.footer-col h2{font-size:14px;font-weight:700;line-height:20px}
.footer-social{display:flex;gap:8px;margin-top:8px}
.footer-social span{width:32px;height:32px;border-radius:50%;background:var(--white)}
.footer-pages{display:grid;grid-template-columns:74px auto}
.footer-brand{position:absolute;left:868px;top:16px;font-size:40px;font-weight:600;line-height:1;letter-spacing:1px}
.copyright{position:absolute;left:869px;top:72px;font-size:12.5px}
</style>
</head>
<body>
<div class="page">
  <div class="top-band"></div>
  <header>
    <div class="brand-name">Vantor-i</div>
    <div class="social-top" role="img" aria-label="Social network links">
      <span class="social-dot"></span><span class="social-dot"></span><span class="social-dot"></span><span class="social-dot active"></span>
    </div>
    <nav class="main-nav">
      <a href="#">HOME</a><a href="#">ABOUT</a><a href="#">SERVICES</a><a href="#">PARTNERS</a><a href="#" class="current">CONTACT</a>
    </nav>
    <div class="header-rule"></div>
  </header>

  <h1 class="page-title">Contact Us</h1>
  <p class="intro">Sed ut perspiciatis unde omnis iste natus error sit voluptatem accusantium doloremque laudantium, totam rem aperiam, eaque ipsa quae ab illo inventore veritatis et quasi architecto beatae vitae dicta sunt explicabo.</p>

  <form class="contact-form">
    <h2 class="section-title">Contact Form</h2>
    <label class="field-label">Name:</label>
    <div class="field">Enter you name</div>
    <label class="field-label">Email Address:</label>
    <div class="field">Enter your email</div>
    <label class="field-label" style="margin-top:10px">Message:</label>
    <div class="field message">Enter Message</div>
    <button type="button" class="submit">Submit</button>
  </form>

  <section class="details">
    <h2 class="section-title">Contact Details</h2>
    <p class="address">Level 4, 18 Harlow Lane<br>Melbourne<br>Australia, 3000</p>
    <ul class="detail-list">
      <li><svg viewBox="0 0 22 22"><circle cx="11" cy="11" r="11" fill="var(--brand)"/><path d="M5 10c0-3 12-3 12 0l-2 1-1-2h-6l-1 2z M7 12h8l1 4H6z" fill="#fff"/></svg>+61 3 555 0142</li>
      <li><svg viewBox="0 0 22 22"><circle cx="11" cy="11" r="11" fill="var(--brand)"/><rect x="7" y="5" width="8" height="4" fill="#fff"/><rect x="5" y="10" width="12" height="5" fill="#fff"/><rect x="7" y="14" width="8" height="3" fill="#fff"/></svg>+61 3 555 0187</li>
      <li><svg viewBox="0 0 22 22"><circle cx="11" cy="11" r="11" fill="var(--brand)"/><circle cx="11" cy="11" r="4" fill="#fff"/></svg>@vantor-i</li>
      <li><svg viewBox="0 0 22 22"><circle cx="11" cy="11" r="11" fill="var(--brand)"/><rect x="5" y="7" width="12" height="8" fill="none" stroke="#fff" stroke-width="1.5"/><path d="M5 7l6 5 6-5" fill="none" stroke="#fff" stroke-width="1.5"/></svg>info@vantor-i.example</li>
    </ul>
  </section>

  <footer class="site-footer">
    <div class="footer-col" style="left:121px">
      <h2>CONNECT WITH US</h2>
      <p>on social media network</p>
      <div class="footer-social" role="img" aria-label="Social network links"><span></span><span></span><span></span><span></span></div>
    </div>
    <div class="footer-col" style="left:331px">
      <h2>PAGES</h2>
      <div class="footer-pages">
        <span>Home</span><span>Term &amp; Conditions</span>
        <span>About</span><span>FAQ</span>
        <span>Services</span><span>Porfolio</span>
      </div>
    </div>
    <div class="footer-col" style="left:569px">
      <h2>CONTACT DETAILS</h2>
      <p>p: +61 3 555 0142&nbsp; f: +61 3 555 0187<br>Level 4, 18 Harlow Lane Melbourne,<br>Australia, 3000</p>
    </div>
    <div class="footer-brand">Vantor-i</div>
    <p class="copyright">Copyright © 2014 All Rights Reserved</p>
  </footer>
</div>
</body>
</html>
```